Holiday Rental Company Flyer Design (DL not A5)

Note from Brandloom Administration: The category sizing selected is A5, however the project requires DL sized artwork. Please refer to the DL template link below while the 'Special Requirements' are updated accordingly.

Project Brief:
We need a double sided DL flyer designed for an up market Holiday Rental Company that portrays a personalised approach to property management. These are to be used for letter box drops to homes we're specifically targeting so the design should be modern, complimentary colour palette, uncluttered & visually appealing.

Please Download the DL Template from Quillora here: http://www.quillora.com.au/ql/ns/propath/UploadResources.aspx?selectedTab=0?pfid=KMT&pf_id=KMT&xnav=easypath-upload-image#Templates

Target Market(s)

Wealthy Home Owners

Industry/Entity Type

It Company

Other font styles liked:
• Avant Garde Extra Light & Demi

Colors
33b8a4

Requirements
Must have
• DL Flyer sizes (210mm width x 99mm width, plus 3mm bleed)
• Front: Logo, Main Image & Grab
• Back: Contact Details & Brief Description of our business
• Images: Ideally the main image should be the house with the pool but alternatively a lifestyle images could also be used.
Nice to have
• A creative designer!
Should not have
• Clutter & busy designs

```html
<!DOCTYPE html>
<html lang="en">
<head>
<meta charset="utf-8">
<title>Harbourline Stays – DL Flyer</title>
<link href="https://fonts.googleapis.com/css2?family=Roboto+Condensed:wght@300;400&family=Lato:wght@300;400;700&display=swap" rel="stylesheet">
<style>
  :root {
    --page-bg: #ececec;
    --teal: #33b8a4;
    --teal-soft: rgba(51, 184, 164, 0.82);
    --sky-top: #7d8fc6;
    --sky-mid: #a9b7d6;
    --sea: #7fb6c4;
    --sea-deep: #4f8ea3;
    --white: #ffffff;
    --ink: #1e1e1e;
    --grey: #7a7a7a;
    --rule: #b9b9b9;
  }
  * { box-sizing: border-box; margin: 0; padding: 0; }
  html, body { width: 1200px; height: 949px; overflow: hidden; }
  body { background: var(--page-bg); position: relative; font-family: "Lato", sans-serif; }

  .flyer { position: absolute; top: 127px; width: 337px; height: 699px; overflow: hidden; background: var(--white); }
  .flyer--front { left: 238px; }
  .flyer--back { left: 625px; }

  .brand-name { position: absolute; left: 0; right: 0; color: var(--white);
    font-family: "Roboto Condensed", sans-serif; font-weight: 400; font-size: 26px;
    letter-spacing: 0.5px; text-align: center; line-height: 1; white-space: nowrap; }

  /* Front */
  .front-photo { position: absolute; inset: 0;
    background: linear-gradient(180deg, var(--sky-top) 0%, var(--sky-mid) 45%, #c9d2e2 66%, var(--sea) 70%, var(--sea-deep) 82%); }
  .front-disc { position: absolute; left: 40px; top: 112px; width: 250px; height: 250px; border-radius: 50%; background: var(--teal-soft); }
  .flyer--front .brand-name { top: 224px; }
  .tagline-band { position: absolute; left: 0; right: 0; bottom: 0; height: 129px; background: var(--teal-soft);
    color: var(--white); font-family: "Roboto Condensed", sans-serif; font-weight: 300; font-size: 21.5px;
    text-align: center; line-height: 27px; padding-top: 16px; }

  /* Back */
  .back-photo { position: absolute; left: 0; right: 0; top: 0; height: 227px;
    background: linear-gradient(180deg, #8f96a8 0%, #aeb6c4 45%, #9fb3c2 62%, #6f98ab 100%); }
  .flyer--back .brand-name { top: 86px; }
  .info-panel { position: absolute; left: 0; right: 0; top: 227px; height: 363px; background: var(--white); }
  .section-title { position: absolute; top: 24px; left: 14px; right: 14px; display: flex; align-items: center; gap: 10px;
    color: var(--teal); font-family: "Roboto Condensed", sans-serif; font-weight: 400; font-size: 15px; white-space: nowrap; }
  .section-title::before, .section-title::after { content: ""; flex: 1; height: 1px; background: var(--rule); }
  .intro { position: absolute; top: 56px; left: 12px; right: 10px; text-align: center; color: var(--grey); font-size: 10px; line-height: 15px; }
  .lead { position: absolute; top: 97px; left: 15px; right: 10px; color: var(--ink); font-size: 10.6px; font-weight: 700; line-height: 15px; }
  .benefit { position: absolute; left: 0; right: 0; text-align: center; color: var(--grey); font-size: 10px; }
  .benefit svg { display: block; margin: 0 auto 6px; }
  .benefit--home { top: 149px; }
  .benefit--rapport { top: 211px; }
  .benefit--bond { top: 278px; }

  .contact-band { position: absolute; left: 0; right: 0; top: 590px; bottom: 0;
    background: linear-gradient(180deg, #9aa6c6 0%, #b7c0d6 55%, #c9cfde 100%); }
  .contact-note { position: absolute; top: 9px; left: 15px; right: 12px; color: var(--white); font-size: 9.4px; line-height: 12.5px; }
  .contact-list { position: absolute; top: 43px; left: 104px; list-style: none; color: var(--white); font-size: 9.6px; }
  .contact-list li { display: flex; align-items: center; gap: 6px; height: 19px; }
</style>
</head>
<body>

<section class="flyer flyer--front" aria-label="Flyer front">
  <div class="front-photo" role="img" aria-label="Photo of an outrigger sailboat with a white sail on a calm turquoise sea under a blue cloudy sky"></div>
  <div class="front-disc"></div>
  <h1 class="brand-name">Harbourline Stays</h1>
  <p class="tagline-band">HOLIDAY RENTAL<br>MANAGEMENT<br>WITH A DIFFERENCE</p>
</section>

<section class="flyer flyer--back" aria-label="Flyer back">
  <div class="back-photo" role="img" aria-label="Photo of a lone sailboat mast reflected on a still sea at dusk"></div>
  <h2 class="brand-name">Harbourline Stays</h2>

  <div class="info-panel">
    <h3 class="section-title">WHAT WE DO DIFFERENTLY!</h3>
    <p class="intro">Rather than relying upon a key safe or a central pickup destination, a ‘Harbourline Stays’ staff member will greet guests upon arrival.</p>
    <p class="lead">Our ‘Meet &amp; Greet’ service provides home owners with an increased level of Security and also allows us to:</p>

    <div class="benefit benefit--home">
      <svg width="32" height="26" viewBox="0 0 32 26" fill="none" stroke="var(--teal)" stroke-width="2">
        <path d="M2 13 L16 2 L30 13"/><path d="M6 10 V24 H26 V10"/><path d="M13 24 V16 H19 V24"/><path d="M23 4 V8"/>
      </svg>
      Prepare the home for their arrival (lights, heaters, music etc.);
    </div>

    <div class="benefit benefit--rapport">
      <svg width="28" height="32" viewBox="0 0 28 32" fill="none" stroke="var(--teal)" stroke-width="1.6">
        <circle cx="14" cy="5" r="3.5"/><path d="M9 15 V11 H19 V15"/><path d="M3 16 H25"/>
        <path d="M14 16 V22 M6 16 V24 M22 16 V24"/><circle cx="6" cy="27" r="2.5"/><circle cx="14" cy="25" r="2.5"/><circle cx="22" cy="27" r="2.5"/>
      </svg>
      Establish a rapport &amp; help facilitate future bookings;
    </div>

    <div class="benefit benefit--bond">
      <svg width="32" height="30" viewBox="0 0 32 30" fill="none" stroke="var(--teal)" stroke-width="1.8">
        <circle cx="16" cy="15" r="4" fill="var(--teal)"/>
        <path d="M16 15 L5 4 M16 15 L27 4 M16 15 L5 26 M16 15 L27 26 M16 15 L16 4"/>
        <circle cx="5" cy="4" r="2.5" fill="var(--teal)"/><circle cx="27" cy="4" r="2.5" fill="var(--teal)"/>
        <circle cx="5" cy="26" r="2.5" fill="var(--teal)"/><circle cx="27" cy="26" r="2.5" fill="var(--teal)"/>
      </svg>
      Reiterate their responsibilities to ensure the return of their bond.
    </div>
  </div>

  <div class="contact-band" role="img" aria-label="Soft photo of a cloudy sky over the sea">
    <p class="contact-note">If you’d like to know what your property could achieve or require additional information, please contact us on:</p>
    <ul class="contact-list">
      <li>
        <svg width="13" height="13" viewBox="0 0 14 14" fill="none" stroke="var(--white)" stroke-width="1.2"><circle cx="7" cy="7" r="6.2"/><path d="M4.5 3.8 L5.8 3.5 L6.5 5.3 L5.7 6 Q6.5 7.6 8 8.3 L8.7 7.5 L10.5 8.2 L10.2 9.5 Q7 10 4.5 3.8Z" fill="var(--white)"/></svg>
        (03)5900 0172
      </li>
      <li>
        <svg width="13" height="10" viewBox="0 0 14 10" fill="none" stroke="var(--white)" stroke-width="1.2"><rect x="0.6" y="0.6" width="12.8" height="8.8"/><path d="M0.6 0.6 L7 5.5 L13.4 0.6"/></svg>
        stay@harbourlinestays.com.au
      </li>
      <li>
        <svg width="13" height="13" viewBox="0 0 14 14" fill="none" stroke="var(--white)" stroke-width="1.1"><circle cx="7" cy="7" r="6.2"/><ellipse cx="7" cy="7" rx="2.8" ry="6.2"/><path d="M0.8 7 H13.2 M2 3.8 H12 M2 10.2 H12"/></svg>
        harbourlinestays.com.au
      </li>
    </ul>
  </div>
</section>

</body>
</html>
```